Business Card Design for company

We want new business cards. We'd like something different-- yet still highly professional. Our tagline is Providing leadership, delivering success. Stock photos are ok, as long as they are relevant and look upscale.

Target Market(s)

Architecture/Business Management Consulting/Engineering Consulting

Contact Information for Business Card

dark gray background with pops of blue might be good, but you tell me. You're the designers. Rounded corners might be nice, but again, you tell me.

Font styles to use
Serif
Sans Serif

Colors
3276b5
5c5c5c
9d9d9d
fbfbfb

Requirements
Nice to have
• Something different, but still very professional.

```html
<!DOCTYPE html>
<html lang="en">
<head>
<meta charset="UTF-8">
<title>Norvale International – Business Card</title>
<link rel="stylesheet" href="https://fonts.googleapis.com/css2?family=Montserrat:wght@500;600;700&display=swap">
<style>
  :root {
    --stage: #1c1c1e;
    --card: #4a4d54;
    --card-back: #45484f;
    --pattern: #3f4248;
    --blue: #3276b5;
    --white: #fbfbfb;
    --muted: #9d9d9d;
  }
  * { box-sizing: border-box; margin: 0; padding: 0; }
  html, body {
    width: 1200px;
    height: 900px;
    overflow: hidden;
    background: var(--stage);
    font-family: "Montserrat", sans-serif;
  }
  .stage {
    width: 1200px;
    height: 900px;
    display: flex;
    flex-direction: column;
    align-items: center;
    justify-content: center;
    gap: 40px;
  }
  .card {
    width: 700px;
    height: 400px;
    border-radius: 6px;
    position: relative;
    overflow: hidden;
  }

  /* Back side */
  .card--back { background: var(--card-back); }
  .card--back .pattern-field {
    position: absolute;
    inset: 0;
    background: linear-gradient(100deg, var(--pattern) 0%, #4b4e55 100%);
  }
  .card--back .brand-name {
    position: absolute;
    left: 50%;
    top: 50%;
    transform: translate(-50%, -50%);
    font-weight: 700;
    font-size: 30px;
    letter-spacing: 1px;
    color: var(--white);
  }

  /* Front side */
  .card--front {
    background: var(--card);
    display: flex;
    align-items: center;
    padding: 0 50px 0 56px;
  }
  .brand-block {
    width: 290px;
    color: var(--white);
    font-weight: 700;
    text-transform: uppercase;
  }
  .brand-block .brand-main {
    display: block;
    font-size: 52px;
    line-height: 1;
    letter-spacing: 1px;
  }
  .brand-block .brand-sub {
    display: block;
    font-size: 27px;
    letter-spacing: 2px;
    margin-top: 8px;
  }
  .divider {
    width: 2px;
    height: 205px;
    background: var(--white);
    margin: 0 34px 0 18px;
  }
  .contact { color: var(--white); }
  .contact .person-name {
    color: var(--blue);
    font-weight: 600;
    font-size: 21px;
    letter-spacing: 2px;
    text-transform: uppercase;
  }
  .contact .person-role {
    font-size: 14px;
    font-weight: 500;
    margin-top: 2px;
  }
  .contact address {
    font-style: normal;
    font-size: 16px;
    font-weight: 500;
    line-height: 1.45;
    letter-spacing: 0.5px;
    margin-top: 18px;
  }
  .contact-list {
    list-style: none;
    margin-top: 14px;
    font-size: 16px;
    font-weight: 500;
    letter-spacing: 0.5px;
  }
  .contact-list li {
    display: flex;
    align-items: center;
    gap: 10px;
    line-height: 1.7;
  }
  .contact-list svg { width: 12px; height: 12px; flex: none; }
</style>
</head>
<body>
<main class="stage">
  <section class="card card--back" aria-label="Card back">
    <div class="pattern-field" role="img" aria-label="Faint repeating company name pattern in dark grey"></div>
    <span class="brand-name">Norvale</span>
  </section>

  <section class="card card--front" aria-label="Card front">
    <div class="brand-block">
      <span class="brand-main">Norvale</span>
      <span class="brand-sub">International</span>
    </div>
    <div class="divider"></div>
    <div class="contact">
      <p class="person-name">Daniel Hartley</p>
      <p class="person-role">Director</p>
      <address>218b Marlow Street,<br>Christchurch, NZ, 8014</address>
      <ul class="contact-list">
        <li>
          <svg viewBox="0 0 12 12" aria-hidden="true"><path d="M2.5 1 L4.5 1 L5.2 3.4 L4 4.4 Q5.2 7 7.6 8 L8.6 6.8 L11 7.5 L11 9.5 Q11 11 9.5 11 Q1 10.5 1 2.5 Q1 1 2.5 1 Z" fill="var(--blue)"/></svg>
          (555) 014-2876
        </li>
        <li>
          <svg viewBox="0 0 12 12" aria-hidden="true"><rect x="0.5" y="2.5" width="11" height="7" rx="1" fill="var(--blue)"/><path d="M1 3 L6 7 L11 3" stroke="var(--card)" stroke-width="1" fill="none"/></svg>
          info@norvaleintl.com
        </li>
        <li>
          <svg viewBox="0 0 12 12" aria-hidden="true"><circle cx="6" cy="6" r="5" fill="var(--blue)"/><path d="M1 6 H11 M6 1 Q3 6 6 11 M6 1 Q9 6 6 11" stroke="var(--card)" stroke-width="0.8" fill="none"/></svg>
          www.norvaleintl.com
        </li>
      </ul>
    </div>
  </section>
</main>
</body>
</html>
```